Personal Care and Home care ingredients Brochure

We need a flyer or brochure of the of chemicals we distribute for the manufacturing of personal care products such as shampoos, liquid soaps, creams, lotions, conditioners, hand sanitizer, Hair Jellys, etc and for Home care products such as, liquid soaps, desinfectants, cleaners, stain removers,etc.
The idea is to send this pdf brochure via email and companies feel very confortable with the impression it gives. We want to call attention.
Target Market(s)
Companies that manufactures cosmetics, personal care products and home care products.
Font styles to use
Colors
Designer to choose colors to be used in the design.
Requirements
Must have
- Images that refers to the skin, hair, cleaning, washing

```html
<!DOCTYPE html>
<html lang="es">
<head>
<meta charset="utf-8">
<title>Ingredientes para Cuidado Personal y Cuidado del Hogar</title>
<link rel="stylesheet" href="https://fonts.googleapis.com/css2?family=Arvo:wght@700&family=Source+Sans+3:wght@400;600;700&display=swap">
<style>
  :root {
    --teal: #1f9a7e;
    --teal-dark: #1e8c78;
    --mint: #62c5a6;
    --mint-deep: #2a9c84;
    --panel: #eef7f5;
    --ink: #2b2b2b;
    --navy: #1f2833;
    --paper: #ffffff;
  }
  * { margin: 0; padding: 0; box-sizing: border-box; }
  html, body { width: 900px; height: 1200px; overflow: hidden; background: var(--paper); }
  .flyer {
    position: relative; width: 900px; height: 1200px; overflow: hidden;
    background: var(--paper);
    font-family: "Source Sans 3", sans-serif; color: var(--ink);
  }
  .header-photo {
    position: absolute; left: 0; top: 0; width: 900px; height: 338px;
    background: linear-gradient(100deg, #f4f4f2 0%, #f6dccd 30%, #f3e7df 50%, #f2f2ef 72%, #e6efe8 100%);
  }
  .header-ribbons { position: absolute; left: 0; top: 0; width: 900px; height: 338px; }
  .title {
    position: absolute; left: 0; top: 196px; width: 900px; text-align: center;
    font-family: "Arvo", serif; font-weight: 700; font-size: 50px; line-height: 60px;
    color: var(--teal-dark);
    text-shadow: 2px 2px 0 #fff, 3px 4px 5px rgba(0,0,0,.35);
  }
  .header-band { position: absolute; left: 0; top: 336px; width: 900px; height: 14px; background: var(--mint); }
  .side-panel { position: absolute; left: 0; top: 350px; width: 440px; height: 740px; }
  .column { position: absolute; top: 380px; }
  .column--left { left: 56px; width: 380px; }
  .column--right { left: 468px; width: 420px; top: 378px; }
  .group-title {
    color: var(--teal); font-weight: 600; font-size: 17px; letter-spacing: .2px;
    margin: 10px 0 9px;
  }
  .group-title:first-child { margin-top: 0; }
  .items { list-style: none; margin-bottom: 8px; }
  .items li { font-size: 17px; line-height: 20.6px; padding-left: 16px; position: relative; }
  .items li::before {
    content: ""; position: absolute; left: 1px; top: 8px; width: 7px; height: 7px;
    border-radius: 50%; background: var(--ink);
  }
  .items small { font-size: 13.5px; }
  .items--accent li { color: var(--teal); font-weight: 700; }
  .items--accent li::before { background: var(--teal); top: 5px; }
  .bottom-corner { position: absolute; left: 0; bottom: 0; width: 340px; height: 190px; }
  .partner {
    position: absolute; font-family: "Source Sans 3", sans-serif; font-weight: 700;
    white-space: nowrap; color: var(--ink); font-size: 30px;
  }
  .partner--lumen { left: 500px; top: 974px; }
  .partner--kelmar { left: 500px; top: 1040px; }
  .partner--selvane { left: 712px; top: 1040px; }
  .partner--norvak { left: 712px; top: 1096px; }
  .partner--arkon { left: 300px; top: 1118px; }
  .partner--aromira { left: 520px; top: 1118px; }
</style>
</head>
<body>
<div class="flyer">
  <div class="header-photo" role="img" aria-label="Fotografía de dispensador de jabón, toallas enrolladas, vaso de baño y planta suculenta"></div>
  <svg class="header-ribbons" viewBox="0 0 900 338" aria-hidden="true">
    <polygon points="318,0 420,0 640,150 540,150" fill="#62c5a6"/>
    <polygon points="560,0 700,0 640,150 540,150" fill="#2a9c84"/>
    <polygon points="700,0 790,0 900,110 900,200" fill="#62c5a6" opacity=".85"/>
    <polygon points="790,0 900,0 900,110" fill="#4fb596"/>
  </svg>
  <h1 class="title">Ingredientes para Cuidado<br>Personal y Cuidado del Hogar</h1>
  <div class="header-band"></div>

  <svg class="side-panel" viewBox="0 0 440 740" aria-hidden="true">
    <path d="M0,0 H428 V520 Q420,700 300,740 H0 Z" fill="#eef7f5"/>
  </svg>

  <section class="column column--left">
    <h2 class="group-title">ALCOHOLES GRASOS</h2>
    <ul class="items">
      <li>Alcohol Cetilico</li>
      <li>Alcohol Ceto-Estearilico</li>
      <li>Alcohol Estearilico</li>
      <li>Alcohol Laurico</li>
      <li>Alcohol Miristilico</li>
    </ul>
    <h2 class="group-title">ACIDOS GRASOS</h2>
    <ul class="items">
      <li>Acido Estearico Triple Prensado</li>
      <li>Acido Oleico</li>
      <li>Acido Palmitic</li>
    </ul>
    <ul class="items items--accent" style="margin-top:14px">
      <li>BUTIL GLICOL</li>
      <li>GLICERINA</li>
      <li>PROPILEN GLICOL</li>
      <li>TRIETANOLAMINA</li>
    </ul>
    <h2 class="group-title">AMIDAS</h2>
    <ul class="items">
      <li>Cocoamida DEA</li>
      <li>Cocoamida MEA</li>
      <li>Cocoamido propil Betaina (CAPB)</li>
    </ul>
    <h2 class="group-title">VITAMINA E</h2>
    <ul class="items">
      <li>Tocotrienoles</li>
    </ul>
    <h2 class="group-title">FRAGANCIAS de AROMIRA ESPAÑA</h2>
    <ul class="items">
      <li>Para cuidado Personal</li>
      <li>Para cuidado del Hogar</li>
    </ul>
  </section>

  <section class="column column--right">
    <h2 class="group-title">ESTERES</h2>
    <ul class="items">
      <li>Estearato de Glicol (EGS)</li>
      <li>Diestearoto de Glicol (EGDS)</li>
      <li>Triglicerido Caprilico / Caprico</li>
      <li>Palmitato de etil Hexilo (EHP)</li>
      <li>Palmitato de Isopropilo (IPP)</li>
      <li>Palmitato de Miristato (IPM)</li>
    </ul>
    <h2 class="group-title">SURFACTANTES ANIONICOS</h2>
    <ul class="items">
      <li>Sulfonatos de Ester Metilico <small>(MES)</small></li>
      <li>Viruta de Jabon <small>( Soap Noodles / Soap Bases)</small></li>
      <li>Lauril Eter Sulfato de Sodio <small>(SLES)</small></li>
      <li>Lauril Sulfato de Sodio <small>(SLS)</small></li>
      <li>Lauril Sulfosuccinato de Sodio <small>(Surfactante Suave)</small></li>
      <li>Base para Jabones Sinteticos <small>(Syndets)</small></li>
      <li>Acido Alquilbenceno Sulfonico Lineal <small>(LABSA)</small></li>
    </ul>
    <h2 class="group-title">NUESTROS ALIADOS COMERCIALES:</h2>
    <ul class="items">
      <li>NORVAK</li>
      <li>SELVANE</li>
      <li>ARKON VALE</li>
      <li>KELMAR OLEO</li>
      <li>LUMEN CHEMICAL</li>
      <li>AROMIRA</li>
    </ul>
  </section>

  <svg class="bottom-corner" viewBox="0 0 340 190" aria-hidden="true">
    <polygon points="0,0 0,190 150,190" fill="#1f2833"/>
    <polygon points="30,30 110,30 270,190 190,190" fill="#62c5a6" opacity=".9"/>
    <polygon points="110,30 140,30 300,190 270,190" fill="#2a9c84" opacity=".6"/>
  </svg>

  <div class="partner partner--lumen">Lumen Chem</div>
  <div class="partner partner--kelmar">Kelmar Oleo</div>
  <div class="partner partner--selvane">Selvane</div>
  <div class="partner partner--norvak">Norvak</div>
  <div class="partner partner--arkon">Arkon Vale</div>
  <div class="partner partner--aromira">Aromira</div>
</div>
</body>
</html>
```